Oil Field Service company needs professional business cards

Looking to clean up our current company business cards and look a little more professional. Brenwick Casing Services is a US based company that services the oil field. We deal with engineers, managers and oil rigs....................................................................................................................................................................................................................................................................................................................................................................................................

Target Market(s)

Oil and Gas professionals

Industry/Entity Type

Oil And Gas

Contact Information for Business Card

See attached photo as example

Font styles to use
Sans Serif

Colors
ec1f27

Requirements
Must have
• Company Logo, Name, Title, Cell, Office, Fax, Email.
• See attached photo
Nice to have
• External CRT, Internal CRT, Casing Crews, Torque Turn, Laydown Machine
Should not have
• Do not introduce any new pictures and keep it professional looking

```html
<!DOCTYPE html>
<html lang="en">
<head>
<meta charset="utf-8">
<title>Brenwick Casing Services – Business Card</title>
<link href="https://fonts.googleapis.com/css2?family=Roboto:wght@400;700;900&family=Roboto+Condensed:wght@400;700&display=swap" rel="stylesheet">
<style>
  :root {
    --red: #d2221f;
    --slate: #3f5366;
    --paper: #f7f7f7;
    --white: #ffffff;
    --backdrop: #e6e6e6;
  }
  * { box-sizing: border-box; margin: 0; padding: 0; }
  html, body {
    width: 1200px; height: 576px; overflow: hidden;
    background: var(--backdrop);
    font-family: "Roboto", Arial, sans-serif;
  }
  .canvas { position: relative; width: 1200px; height: 576px; }
  .card {
    position: absolute; overflow: hidden; border-radius: 6px;
    box-shadow: 0 2px 4px rgba(0,0,0,.18);
  }

  /* Front */
  .card-front { left: 82px; top: 139px; width: 485px; height: 293px; background: var(--paper); }
  .front-brand { position: absolute; top: 62px; left: 0; width: 100%; text-align: center; color: var(--slate); font-weight: 900; }
  .front-brand .brand-main { display: block; font-size: 54px; line-height: 1; letter-spacing: 1px; }
  .front-brand .brand-sub { display: block; font-size: 19px; letter-spacing: 3px; margin-top: 22px; }
  .front-services {
    position: absolute; top: 221px; left: 0; width: 100%; height: 27px;
    background: var(--red); color: var(--white);
    display: flex; align-items: center; justify-content: center; gap: 8px;
    font-size: 13.5px; font-weight: 700; letter-spacing: .2px;
  }
  .front-web {
    position: absolute; top: 262px; left: 0; width: 100%;
    display: flex; align-items: center; justify-content: center; gap: 10px;
    font-size: 14px; color: var(--slate);
  }
  .front-web .rule { width: 78px; height: 2px; background: var(--red); }
  .front-web .rule.left { background: linear-gradient(to right, transparent, var(--red)); }
  .front-web .rule.right { background: linear-gradient(to left, transparent, var(--red)); }

  /* Back */
  .card-back { left: 602px; top: 138px; width: 482px; height: 291px; background: var(--red); }
  .back-shape { position: absolute; inset: 0; }
  .person { position: absolute; left: 26px; top: 42px; color: var(--white); }
  .person-name { font-family: "Roboto Condensed", Arial, sans-serif; font-size: 23px; font-weight: 700; line-height: 1.1; }
  .person-title { font-size: 11.5px; margin-top: 3px; }
  .contact-list { position: absolute; left: 26px; top: 128px; list-style: none; color: var(--white); font-size: 11.5px; }
  .contact-list li { display: flex; align-items: center; gap: 7px; height: 16.2px; }
  .contact-list svg { width: 10px; height: 10px; fill: var(--white); flex: none; }
  .back-services {
    position: absolute; left: 26px; top: 245px; height: 27px;
    display: flex; align-items: center; gap: 5px;
    font-family: "Roboto Condensed", Arial, sans-serif; font-size: 12.5px; color: var(--white);
  }
  .back-brand {
    position: absolute; left: 406px; top: 146px; width: 0; height: 0;
  }
  .back-brand-inner {
    position: absolute; left: 0; top: 0; transform: translate(-50%, -50%) rotate(-90deg);
    white-space: nowrap; text-align: center; color: var(--slate); font-weight: 900;
  }
  .back-brand .brand-main { display: block; font-size: 33px; line-height: 1; letter-spacing: .5px; }
  .back-brand .brand-sub { display: block; font-size: 12px; letter-spacing: 2.5px; margin-top: 9px; }
</style>
</head>
<body>
<main class="canvas">

  <section class="card card-front" aria-label="Card front">
    <h1 class="front-brand">
      <span class="brand-main">BRENWICK</span>
      <span class="brand-sub">CASING SERVICES</span>
    </h1>
    <div class="front-services">
      <span>LAYDOWN MACHINE</span><span>|</span><span>CASING CREW</span><span>|</span><span>MUD TOOL</span><span>|</span><span>TORQUE TURN</span>
    </div>
    <div class="front-web">
      <span class="rule left"></span><span>www.brenwicksrvs.com</span><span class="rule right"></span>
    </div>
  </section>

  <section class="card card-back" aria-label="Card back">
    <svg class="back-shape" viewBox="0 0 482 291" preserveAspectRatio="none">
      <rect x="0" y="245" width="482" height="27" fill="var(--slate)"/>
      <path d="M346 0 L360 0 Q300 90 306 210 Q302 100 346 0 Z" fill="var(--slate)"/>
      <path d="M382 0 Q296 150 352 291 L482 291 L482 0 Z" fill="var(--paper)"/>
    </svg>

    <div class="person">
      <h2 class="person-name">Cody Harlan</h2>
      <p class="person-title">Area Manager</p>
    </div>

    <ul class="contact-list">
      <li><svg viewBox="0 0 10 10"><path d="M2 .5 3.6 2.6 2.8 3.6Q3.8 5.8 6.4 7.2L7.4 6.4 9.5 8 8.4 9.5Q4.6 9.2 .5 1.6Z"/></svg>(555) 214-5700</li>
      <li><svg viewBox="0 0 10 10"><path d="M.5 3Q5 .5 9.5 3L9 4.5 7 4 7 3Q5 2.4 3 3L3 4 1 4.5Z M2 5.5H8L9 9H1Z"/></svg>(555) 318-7496</li>
      <li><svg viewBox="0 0 10 10"><path d="M2.5 .5H7.5V3H2.5Z M.5 3.5H9.5V7.5H8V6H2V7.5H.5Z M2.5 6.5H7.5V9.5H2.5Z"/></svg>(555) 214-3230</li>
      <li><svg viewBox="0 0 10 10"><path d="M5 .3A3.4 3.4 0 0 1 8.4 3.7C8.4 6 5 9.7 5 9.7S1.6 6 1.6 3.7A3.4 3.4 0 0 1 5 .3ZM5 2.4A1.3 1.3 0 1 0 5 5 1.3 1.3 0 0 0 5 2.4Z"/></svg>Millbrook, OK 73000</li>
      <li><svg viewBox="0 0 10 10"><path d="M.5 2H9.5V8H.5ZM1.2 2.6 5 5.6 8.8 2.6"/></svg>codyharlan@brenwicksrvs.com</li>
      <li><svg viewBox="0 0 10 10"><circle cx="5" cy="5" r="4.5"/><path d="M.8 5H9.2M5 .6V9.4" stroke="var(--red)" stroke-width=".8" fill="none"/></svg>www.brenwicksrvs.com</li>
    </ul>

    <div class="back-services">
      <span>Laydown Machine</span><span>|</span><span>Casing Crew</span><span>|</span><span>Mud Tool</span><span>|</span><span>Torque Turn</span>
    </div>

    <div class="back-brand">
      <div class="back-brand-inner">
        <span class="brand-main">BRENWICK</span>
        <span class="brand-sub">CASING SERVICES</span>
      </div>
    </div>
  </section>

</main>
</body>
</html>
```